Wordpress Web Design & Coding for velcorahealth.ca

We need a website for a new investment company that is visually grabbing and vibrant. We would like to see a web page that displays trust, growth and confidence. Needs to be responsive and mobile friendly for all browsers and coded for both Android & IOS.

Open to the number of pages and menu items. I selected 4 but if you feel the layout would work better with less I am open to this. Need to sell the people (management team/related businesses) and then show where the invested money will be going (upcoming projects).

Company Info:

Vel Cora is an investment company put together by a group of seasoned business professionals who have come together to combine decades of success in the real estate development, management, financing and medical services. The company will be a full service company offering turn key solutions for medical professionals.

Vel-Cora will focus on providing a full range of services via a group of distinct companies to deliver newly emerging needs of the medical community. The end goal will be to create complete solutions for individuals in the medical community. Our group has experience and success with the conceptualization, construction and financing of medical and dental clinic spaces. Vel-Cora Solutions will be established to accommodate all areas of the development and creation of clinics for medical professionals from building construction to equipment financing and administrations.

You can mention these companies and take photos from their websites. You can also use stock photos.

Our construction partner:
https://318bld.com/projects/

Our equipment leasing partner:
https://www.norvixa.com/

Our Management Team and medical partners

Gil Parish
https://www.ourfirmstance.ca/

Dietmar Vellasquin
https://www.gshdentalservices.com/about-us

PROPOSED PROJECTS (see attachment for details)
Pinegrove Business Park
Holtmere Business Park
Mt. Corwin Ridge Professional

Target Market(s)

Investors

Industry/Entity Type

Investment

Coding

Coded - Design and coding required

Number of Pages Required

4 page

Font styles to use
Sans Serif

Requirements
Must have
• Wordpress – must be both desktop and mobile friendly with fast page load speed
Ability to edit after ourselves in Wordpress
Attractive home page with logo etc.
Logo colours are: for the blue the pantone color is #0355a3
and for the green is #8cc63f

Sections, about us, what we do/services we provide, contact us

```html
<!DOCTYPE html>
<html lang="en">
<head>
<meta charset="utf-8">
<title>Vel-Cora Solutions</title>
<link href="https://fonts.googleapis.com/css2?family=Lato:wght@700;900&family=Roboto:wght@400;500&display=swap" rel="stylesheet">
<style>
:root{
  --blue:#0b3e94;
  --blue-deep:#0a3a8c;
  --green:#7cbc2c;
  --green-pale:#eef8df;
  --grey-bg:#f1f1f1;
  --text:#555;
  --dark:#111;
  --white:#fff;
  --line:#c9c9c9;
}
*{box-sizing:border-box;margin:0;padding:0}
html,body{width:1200px;height:3045px;overflow:hidden}
body{position:relative;font-family:'Roboto',sans-serif;color:var(--text);background:var(--white)}
.abs{position:absolute}
.heading{font-family:'Lato',sans-serif;font-weight:900;color:var(--blue);letter-spacing:-0.5px;text-transform:uppercase}
.heading span{color:var(--green)}
.btn{position:absolute;display:flex;align-items:center;justify-content:center;gap:8px;border-radius:30px;background:var(--green);color:var(--white);font-family:'Roboto',sans-serif;font-weight:500;text-transform:uppercase}

/* header */
.top-line{left:0;top:0;width:1200px;height:5px;background:var(--blue)}
.brand{left:111px;top:26px;display:flex;align-items:center;gap:10px}
.brand-mark{width:18px;height:18px;background:var(--green)}
.brand-name{font-family:'Lato',sans-serif;font-weight:900;color:var(--blue);font-size:24px;line-height:24px}
.brand-name small{display:block;font-size:13px;line-height:16px;letter-spacing:2px}
.nav{left:376px;top:40px;display:flex;gap:23px;font-size:15.5px;font-weight:500;color:var(--dark)}
.nav .active{color:var(--green)}
.nav-dot{left:390px;top:21px;width:12px;height:12px;background:var(--blue)}
.search{left:932px;top:42px}
.login{left:979px;top:31px;width:107px;height:39px;font-size:15px}

/* hero */
.hero-photo{left:0;top:99px;width:1200px;height:706px;
  background:linear-gradient(120deg,#1e3760 0%,#3f5a86 25%,#c9b9a3 45%,#dfe3ea 62%,#8aa6cf 80%,#3c5e98 100%);
  clip-path:polygon(0 0,1200px 0,1200px 486px,376px 654px,0 510px)}
.hero-band{left:0;top:0}
.hero-box{left:298px;top:258px;width:607px;height:273px;background:rgba(70,70,70,.35)}
.hero-title{left:298px;top:290px;width:607px;text-align:center;font-family:'Lato',sans-serif;font-weight:900;font-size:44px;color:var(--white);text-shadow:0 2px 4px rgba(0,0,0,.35);letter-spacing:-1px}
.hero-text{left:320px;top:358px;width:563px;text-align:center;font-size:17.5px;line-height:29px;font-weight:500;color:var(--white)}
.hero-cta{left:507px;top:444px;width:187px;height:53px;font-size:17px}
.arrow{width:42px;height:42px;border:2px solid var(--white);border-radius:50%;display:flex;align-items:center;justify-content:center}

/* about */
.about-title{left:111px;top:872px;font-size:37px}
.about-text{left:111px;top:940px;width:462px;font-size:16px;line-height:29px;text-align:justify}
.about-more{left:111px;top:1174px;width:150px;height:44px;font-size:15.5px}
.about-photo{left:660px;top:810px;width:393px;height:399px;border-radius:4px;
  background:linear-gradient(135deg,#6d8fd0 0%,#3b5fa8 40%,#8b8a7c 70%,#2d4f96 100%)}

/* services */
.services-bg{left:0;top:1270px}
.services-title{left:0;top:1424px;width:1200px;text-align:center;font-size:36px}
.divider{height:2px;background:var(--blue)}
.div-mark{width:12px;height:12px;background:var(--blue)}
.svc-icon{width:68px;height:68px;border-radius:50%;background:radial-gradient(circle at 35% 30%,#2a63c6,#0a2f78);display:flex;align-items:center;justify-content:center}
.svc-title{font-size:19.5px;font-weight:500;color:var(--dark)}
.svc-text{font-size:14.5px;line-height:23.5px;width:230px}
.right{text-align:right}
.svc-center{left:478px;top:1571px;width:220px;height:220px;background:var(--blue);border-radius:8px;opacity:.9}

/* contact */
.contact-title{left:0;top:1994px;width:1200px;text-align:center;font-size:36px}
.contact-bg-mark{left:522px;top:2068px;width:120px;height:372px;background:#e3ebf5;opacity:.8}
.info-icon{width:66px;height:66px;border-radius:50%;border:2px solid var(--green);display:flex;align-items:center;justify-content:center}
.info-icon i{width:54px;height:54px;border-radius:50%;background:var(--green);display:flex;align-items:center;justify-content:center}
.info-label{font-size:16px;font-weight:500;color:var(--dark)}
.info-text{font-size:14.5px;line-height:21px}
.field{position:absolute;border:1px solid var(--line);background:rgba(255,255,255,.85);padding:12px 17px;font-size:14.5px;color:#666}
.robot{left:220px;top:2436px;display:flex;align-items:center;gap:14px;font-size:15.5px;color:var(--dark)}
.robot b{width:20px;height:20px;border:2px solid #444;border-radius:3px}
.captcha{left:392px;top:2420px;width:60px;text-align:center;font-size:10px;color:#888}
.captcha i{display:block;width:34px;height:34px;margin:0 auto 4px;border-radius:50%;border:5px solid #4a7de0;border-right-color:#aaa}
.submit{position:absolute;left:554px;top:2435px;width:105px;height:36px;border-radius:20px;background:var(--blue);color:var(--white);font-weight:500;font-size:15px;display:flex;align-items:center;justify-content:center}

/* footer */
.footer-bg{left:0;top:2540px}
.footer-brand{left:720px;top:2615px;width:190px;text-align:center;font-family:'Lato',sans-serif;font-weight:900;color:var(--white);font-size:34px;line-height:34px}
.footer-brand small{display:block;font-size:17px;line-height:24px;letter-spacing:3px}
.f-head{font-size:17px;font-weight:500;color:var(--white)}
.f-list{list-style:none;font-size:15.5px;color:var(--white)}
.f-list li{height:32.5px;display:flex;align-items:center;gap:8px}
.f-list li.multi{height:auto;align-items:flex-start;line-height:21px;margin-bottom:10px}
.newsletter{left:822px;top:2808px;width:266px;height:38px;border-radius:20px;background:var(--white);font-size:14px;color:#666;display:flex;align-items:center;padding-left:16px}
.newsletter b{position:absolute;right:0;top:0;width:93px;height:38px;border-radius:20px;background:var(--green);color:var(--white);font-weight:500;font-size:16px;display:flex;align-items:center;justify-content:center}
.social{width:38px;height:38px;border-radius:50%;background:var(--white)}
.f-rule{left:111px;top:2975px;width:978px;height:1px;background:rgba(255,255,255,.6)}
.copy{left:0;top:2998px;width:1200px;text-align:center;font-size:15.5px;color:var(--white)}
</style>
</head>
<body>

<!-- header -->
<div class="abs top-line"></div>
<div class="abs brand">
  <div class="brand-mark"></div>
  <div class="brand-name">VEL-CORA<small>SOLUTIONS</small></div>
</div>
<div class="abs nav-dot"></div>
<nav class="abs nav">
  <span class="active">Home</span><span>About Us</span><span>Services</span><span>Team</span><span>Partners</span><span>Projects</span><span>Contact Us</span>
</nav>
<svg class="abs search" width="16" height="16" viewBox="0 0 16 16"><circle cx="6.5" cy="6.5" r="4.8" fill="none" stroke="#111" stroke-width="2"/><line x1="10" y1="10" x2="14.5" y2="14.5" stroke="#111" stroke-width="2.4"/></svg>
<div class="btn login">
  <svg width="11" height="13" viewBox="0 0 11 13"><rect x="0" y="5.5" width="11" height="7.5" rx="1" fill="#fff"/><path d="M2.5 5.5V4a3 3 0 0 1 6 0v1.5" fill="none" stroke="#fff" stroke-width="1.6"/></svg>Login
</div>

<!-- hero -->
<div class="abs hero-photo" role="img" aria-label="Business people reviewing financial charts and a tablet on a desk"></div>
<svg class="abs hero-band" width="1200" height="810" viewBox="0 0 1200 810">
  <polygon points="0,609 376,753 1200,585 1200,592 376,801 0,614" fill="#7cbc2c"/>
</svg>
<div class="abs hero-box"></div>
<div class="abs hero-title">VEL - CORA SOLUTIONS</div>
<p class="abs hero-text">Lorem ipsum dolor sit amet, consectetur adipiscing elit, do eiusmod tempor incididunt ut labore et dolore magna aliqua.</p>
<div class="btn hero-cta">Get Started
  <svg width="15" height="15" viewBox="0 0 16 16"><circle cx="8" cy="8" r="8" fill="#fff"/><path d="M6 4.5 9.5 8 6 11.5" fill="none" stroke="#7cbc2c" stroke-width="2.2"/></svg>
</div>
<div class="abs arrow" style="left:32px;top:347px"><svg width="12" height="18" viewBox="0 0 12 18"><path d="M9 2 3 9l6 7" fill="none" stroke="#fff" stroke-width="2"/></svg></div>
<div class="abs arrow" style="left:1129px;top:347px"><svg width="12" height="18" viewBox="0 0 12 18"><path d="M3 2l6 7-6 7" fill="none" stroke="#fff" stroke-width="2"/></svg></div>

<!-- about -->
<h2 class="abs heading about-title">About <span>Us</span></h2>
<p class="abs about-text">Sed ut perspiciatis unde omnis iste natus voluptatem accusantium doloremque laudantium, totam rem aperiam, eaque ipsa quae ab illo inventore veritatis et quasi architecto beatae vitae dicta sunt explicabo. Nemo enim ipsam voluptatem quia voluptas sit aspernatur aut odit aut fugit, sed quia consequuntur magni dolores eos qui ratione voluptatem sequi nesciunt. Neque porro quisquam est, qui dolorem ipsum quia dolor sit amet, consectetur,</p>
<div class="btn about-more">Read More
  <svg width="14" height="14" viewBox="0 0 16 16"><circle cx="8" cy="8" r="8" fill="#fff"/><path d="M6 4.5 9.5 8 6 11.5" fill="none" stroke="#7cbc2c" stroke-width="2.2"/></svg>
</div>
<div class="abs about-photo" role="img" aria-label="Handshake between medical professionals with stacks of coins"></div>

<!-- services -->
<svg class="abs services-bg" width="1200" height="640" viewBox="0 0 1200 640">
  <polygon points="0,196 827,14 1200,170 1200,633 0,633" fill="#f1f1f1"/>
  <polyline points="0,190 827,8 1200,164" fill="none" stroke="#eef8df" stroke-width="8"/>
</svg>
<h2 class="abs heading services-title">Services <span>We Provide</span></h2>
<div class="abs divider" style="left:488px;top:1478px;width:85px"></div>
<div class="abs div-mark" style="left:594px;top:1473px"></div>
<div class="abs divider" style="left:627px;top:1478px;width:85px"></div>

<div class="abs svc-icon" style="left:110px;top:1549px">
  <svg width="34" height="38" viewBox="0 0 34 38" fill="none" stroke="#fff" stroke-width="1.6"><rect x="8" y="3" width="18" height="33"/><path d="M12 8h3M19 8h3M12 14h3M19 14h3M12 20h3M19 20h3M12 26h3M19 26h3M15 36v-5h4v5M2 36h30"/></svg>
</div>
<div class="abs svc-title" style="left:200px;top:1545px">Real Estate Development</div>
<p class="abs svc-text" style="left:201px;top:1583px">Lorem ipsum dolor sit consectetur adipiscing elit, sed do eiusmod tempor incididunt</p>

<div class="abs svc-icon" style="left:110px;top:1702px">
  <svg width="38" height="34" viewBox="0 0 38 34" fill="none" stroke="#fff" stroke-width="1.6"><rect x="3" y="10" width="24" height="14" rx="2"/><circle cx="15" cy="17" r="4"/><path d="M6 6l20-3 2 7"/><ellipse cx="31" cy="16" rx="5" ry="2"/><path d="M26 16v14c0 1 2 2 5 2s5-1 5-2V16M26 21c0 1 2 2 5 2s5-1 5-2M26 26c0 1 2 2 5 2s5-1 5-2"/></svg>
</div>
<div class="abs svc-title" style="left:200px;top:1698px">Financing</div>
<p class="abs svc-text" style="left:201px;top:1736px">Lorem ipsum dolor sit consectetur adipiscing elit, sed do eiusmod tempor incididunt</p>

<div class="abs svc-center" role="img" aria-label="Brand emblem area"></div>

<div class="abs svc-title right" style="left:797px;top:1545px;width:200px">Management</div>
<p class="abs svc-text right" style="left:757px;top:1583px;width:240px">Lorem ipsum dolor sit consectetur adipiscing elit, do eiusmod tempor incididunt ut labore et dolore</p>
<div class="abs svc-icon" style="left:1019px;top:1549px">
  <svg width="38" height="38" viewBox="0 0 38 38" fill="none" stroke="#fff" stroke-width="1.6"><path d="M14 34v-6c-5-3-8-7-8-13a12 12 0 0 1 24 0c0 6-3 10-8 13v6z"/><circle cx="20" cy="15" r="4"/><circle cx="20" cy="15" r="8" stroke-dasharray="3 2"/></svg>
</div>

<div class="abs svc-title right" style="left:797px;top:1698px;width:200px">Medical Services</div>
<p class="abs svc-text right" style="left:757px;top:1736px;width:240px">Lorem ipsum dolor sit consectetur adipiscing elit, do eiusmod tempor incididunt ut labore et dolore</p>
<div class="abs svc-icon" style="left:1019px;top:1702px">
  <svg width="38" height="36" viewBox="0 0 38 36" fill="none" stroke="#fff" stroke-width="1.6"><rect x="4" y="9" width="30" height="25"/><rect x="4" y="4" width="30" height="5"/><path d="M9 14h6v6H9zM23 14h6v6h-6zM15 34v-9h8v9M2 34h34M19 12v6M16 15h6"/></svg>
</div>

<!-- contact -->
<div class="abs contact-bg-mark"></div>
<h2 class="abs heading contact-title">Contact <span>Us</span></h2>
<div class="abs divider" style="left:509px;top:2048px;width:60px"></div>
<div class="abs div-mark" style="left:594px;top:2043px"></div>
<div class="abs divider" style="left:631px;top:2048px;width:60px"></div>

<div class="abs info-icon" style="left:186px;top:2084px"><i>
  <svg width="18" height="24" viewBox="0 0 18 24"><path d="M9 0a9 9 0 0 0-9 9c0 7 9 15 9 15s9-8 9-15a9 9 0 0 0-9-9z" fill="#fff"/><circle cx="9" cy="9" r="3.2" fill="#7cbc2c"/></svg></i></div>
<div class="abs info-label" style="left:267px;top:2080px">Address:</div>
<p class="abs info-text" style="left:267px;top:2108px;width:230px">123, Lorem ipsum dolor sit amet, consectetur elit,</p>

<div class="abs info-icon" style="left:530px;top:2084px"><i>
  <svg width="22" height="22" viewBox="0 0 24 24"><path d="M6.6 10.8a15 15 0 0 0 6.6 6.6l2.2-2.2c.3-.3.7-.4 1-.2 1.1.4 2.3.6 3.6.6.6 0 1 .4 1 1V20c0 .6-.4 1-1 1A17 17 0 0 1 3 4c0-.6.4-1 1-1h3.5c.6 0 1 .4 1 1 0 1.3.2 2.5.6 3.6.1.3 0 .7-.2 1z" fill="#fff"/></svg></i></div>
<div class="abs info-label" style="left:611px;top:2093px">Phone</div>
<p class="abs info-text" style="left:611px;top:2119px">888 888 8888</p>

<div class="abs info-icon" style="left:775px;top:2084px"><i>
  <svg width="26" height="20" viewBox="0 0 26 20"><rect width="26" height="20" rx="2" fill="#fff"/><path d="M1 2l12 9 12-9" fill="none" stroke="#7cbc2c" stroke-width="2"/></svg></i></div>
<div class="abs info-label" style="left:857px;top:2093px">Email:</div>
<p class="abs info-text" style="left:857px;top:2119px">info@vel-cora.net</p>

<div class="field" style="left:188px;top:2193px;width:399px;height:43px">Name</div>
<div class="field" style="left:611px;top:2193px;width:401px;height:43px">Email</div>
<div class="field" style="left:188px;top:2249px;width:399px;height:43px">Phone</div>
<div class="field" style="left:611px;top:2249px;width:401px;height:43px">subjects</div>
<div class="field" style="left:188px;top:2306px;width:824px;height:86px">Message</div>
<div class="abs robot"><b></b>I'm not a Robot</div>
<div class="abs captcha"><i></i>SafeCheck</div>
<div class="submit">SUBMIT</div>

<!-- footer -->
<svg class="abs footer-bg" width="1200" height="505" viewBox="0 0 1200 505">
  <polygon points="0,208 827,7 1200,175 1200,505 0,505" fill="#7cbc2c"/>
  <polygon points="0,218 827,30 1200,185 1200,505 0,505" fill="#0d3f94"/>
</svg>
<div class="abs footer-brand">VEL-CORA<small>SOLUTIONS</small></div>

<div class="abs f-head" style="left:111px;top:2759px">Quick Links</div>
<ul class="abs f-list" style="left:111px;top:2796px">
  <li>» Home</li><li>» About Us</li><li>» Services</li><li>» Projects</li><li>» Contact Us</li>
</ul>

<div class="abs f-head" style="left:319px;top:2757px">Contact Us</div>
<ul class="abs f-list" style="left:319px;top:2800px;width:260px">
  <li class="multi"><svg width="10" height="14" viewBox="0 0 18 24" style="margin-top:4px;flex:none"><path d="M9 0a9 9 0 0 0-9 9c0 7 9 15 9 15s9-8 9-15a9 9 0 0 0-9-9z" fill="#fff"/></svg><span>123, Lorem ipsum dolor sit amet consectetur adipiscing</span></li>
  <li><svg width="13" height="13" viewBox="0 0 24 24"><path d="M6.6 10.8a15 15 0 0 0 6.6 6.6l2.2-2.2c.3-.3.7-.4 1-.2 1.1.4 2.3.6 3.6.6.6 0 1 .4 1 1V20c0 .6-.4 1-1 1A17 17 0 0 1 3 4c0-.6.4-1 1-1h3.5c.6 0 1 .4 1 1 0 1.3.2 2.5.6 3.6.1.3 0 .7-.2 1z" fill="#fff"/></svg>(888) 888-8888</li>
  <li><svg width="14" height="11" viewBox="0 0 26 20"><rect x="1" y="1" width="24" height="18" rx="2" fill="none" stroke="#fff" stroke-width="2"/><path d="M1 2l12 9 12-9" fill="none" stroke="#fff" stroke-width="2"/></svg>Info@Vel-Cora.com</li>
</ul>

<div class="abs f-head" style="left:631px;top:2759px">Important</div>
<ul class="abs f-list" style="left:631px;top:2799px">
  <li>» Terms of Use</li><li>» Site Map</li><li>» Privacy Policy</li><li>» Disclaimer</li>
</ul>

<div class="abs f-head" style="left:820px;top:2760px">Newsletter Subscription</div>
<div class="abs newsletter">Enter your email<b>SUBMIT</b></div>
<div class="abs social" style="left:821px;top:2864px"></div>
<div class="abs social" style="left:864px;top:2864px"></div>
<div class="abs social" style="left:906px;top:2864px"></div>
<div class="abs social" style="left:950px;top:2864px"></div>

<div class="abs f-rule"></div>
<div class="abs copy">© 2020 Vel - Cora. All Rights Reserved</div>

</body>
</html>
```